UX Design for Analytics Web Application

http://velqoranthe.com/
We are tech & consulting company with analytics products (web applications), located at Rio de Janeiro, Brazil.

We are searching a partner do develop UX for our products, i.e, aesthetics, usability, HTML/CSS.

Currently we have a product suite and the goal is to make a pilot re-design project with one of our products.

The product of interest is interactive webapp that aims at data analysis, significantly different from blogs, e-commerce or landing pages.

We do have a software development team but we lack an UX & HTML expert. Currently we use Bootstrap templates but the results are insatisfatory.

So, the project scope is, to develop the arts (UX, aesthetics, etc) along with the code/mockup (HTML/CSS) for one of our product (3 pages).

This is a pilot project and there's potential to rehire for our other products. Code quality is of importance.

More details and specification can be found in attached files.

Target Market(s)

Executives, managers & consultants

Industry/Entity Type

It Company

Coding

Coded - Design and coding required

Number of Pages Required

3 page

Font styles to use
Sans Serif

Requirements
Must have
• (see attached files, prefer the pptx version))
• -Responsive
Nice to have
• (see attached files, prefer the pptx version)
Should not have
• -Avoid Green, Red and Yellow colors. They have a meaning of good, bad and average in our products.

```html
<!DOCTYPE html>
<html lang="en">
<head>
<meta charset="utf-8">
<title>Velqor – Processes Overview</title>
<link href="https://fonts.googleapis.com/css2?family=Open+Sans:wght@300;400;600;700&display=swap" rel="stylesheet">
<style>
  :root {
    --page-bg: #f1f1f1;
    --panel-bg: #ffffff;
    --panel-border: #d9d9d9;
    --text-dark: #333333;
    --text-body: #555555;
    --text-muted: #777777;
    --icon-dark: #3d3d3d;
    --ring-track: #efefef;
    --ring-active: #6aaee0;
    --ring-completed: #8ecad8;
    --ring-completion: #8a94d8;
    --ring-expenses: #2ea4dd;
    --bullet: #2f7fbf;
    --accent-meta: #8aa6c2;
    --page-active: #2f7fbf;
    --cta: #1f5f99;
    --footer-bg: #1b1b1b;
    --footer-text: #ffffff;
    --avatar: #c9b8a6;
  }
  * { box-sizing: border-box; margin: 0; padding: 0; }
  html, body { width: 851px; height: 1200px; overflow: hidden; }
  body {
    background: var(--page-bg);
    font-family: "Open Sans", Arial, sans-serif;
    color: var(--text-dark);
    position: relative;
  }
  .symbols { position: absolute; width: 0; height: 0; }

  /* Header */
  .app-header {
    position: absolute; top: 0; left: 0; width: 851px; height: 77px;
    background: var(--panel-bg);
    box-shadow: 0 1px 3px rgba(0,0,0,.15);
  }
  .menu-toggle { position: absolute; left: 64px; top: 25px; width: 25px; height: 22px; }
  .menu-toggle span { display: block; height: 4px; background: var(--icon-dark); margin-bottom: 5px; border-radius: 1px; }
  .brand { position: absolute; left: 118px; top: 18px; display: flex; align-items: center; gap: 7px; }
  .brand-mark { width: 22px; height: 22px; border-radius: 50%; background: var(--icon-dark); }
  .brand-name { font-size: 26px; font-weight: 700; color: var(--icon-dark); letter-spacing: -.5px; }
  .header-actions { position: absolute; right: 62px; top: 28px; display: flex; gap: 12px; }
  .header-actions svg { width: 19px; height: 19px; fill: var(--icon-dark); }

  /* Panels */
  .panel {
    position: absolute; background: var(--panel-bg);
    border: 1px solid var(--panel-border);
    box-shadow: 0 1px 3px rgba(0,0,0,.12);
  }
  .panel-title { font-size: 18px; font-weight: 400; letter-spacing: .5px; text-align: center; color: var(--text-dark); }

  .overview { left: 64px; top: 102px; width: 724px; height: 270px; }
  .overview .panel-title { height: 44px; line-height: 52px; border-bottom: 1px solid #ececec; }
  .metric { position: absolute; top: 92px; width: 170px; text-align: center; }
  .metric svg { width: 96px; height: 96px; display: block; margin: 0 auto; overflow: visible; }
  .metric-value { font-size: 24px; font-weight: 300; }
  .metric-label { margin-top: 20px; font-size: 11.5px; letter-spacing: .3px; color: var(--text-dark); }

  .activity { left: 64px; top: 390px; width: 722px; height: 202px; }
  .activity .panel-title { margin-top: 20px; }
  .feed-card { position: absolute; top: 71px; width: 196px; height: 82px; border: 1px solid #cfcfcf; background: var(--panel-bg); }
  .feed-avatar {
    position: absolute; left: 9px; top: 14px; width: 52px; height: 52px;
    border-radius: 50%; background: var(--avatar); box-shadow: 0 1px 3px rgba(0,0,0,.3);
  }
  .feed-text { position: absolute; left: 68px; top: 18px; width: 122px; font-size: 8.3px; line-height: 13px; color: var(--text-body); }
  .feed-meta { margin-top: 5px; font-size: 7.6px; color: var(--text-body); display: flex; align-items: center; gap: 4px; }
  .feed-meta i { display: inline-block; width: 7px; height: 7px; background: var(--accent-meta); border-radius: 1px; }
  .feed-meta i.person { border-radius: 50% 50% 2px 2px; }

  /* Process grid */
  .process-grid {
    position: absolute; left: 64px; top: 608px;
    display: grid; grid-template-columns: repeat(3, 231px);
    grid-auto-rows: 140px; column-gap: 15px; row-gap: 15px;
  }
  .process-card {
    background: var(--panel-bg); border: 1px solid var(--panel-border);
    box-shadow: 0 1px 3px rgba(0,0,0,.12);
    padding: 12px 0 0 13px; font-size: 10.6px; color: var(--text-dark);
  }
  .process-row { display: flex; align-items: center; gap: 7px; height: 19.5px; }
  .bullet { width: 8px; height: 8px; flex: none; }
  .process-desc { padding-left: 15px; width: 205px; font-size: 8.2px; line-height: 13px; color: var(--text-body); margin: 2px 0 5px; }

  /* Pagination */
  .pagination { position: absolute; left: 67px; top: 1078px; display: flex; gap: 6px; }
  .pagination span {
    height: 19px; min-width: 19px; padding: 0 5px; line-height: 17px;
    border: 1px solid #d7d7d7; background: var(--panel-bg);
    font-size: 8.5px; color: var(--text-muted); text-align: center;
  }
  .pagination .wide { padding: 0 8px; }
  .pagination .current { background: var(--page-active); border-color: var(--page-active); color: #fff; }
  .new-process {
    position: absolute; left: 687px; top: 1074px; width: 101px; height: 26px;
    background: var(--cta); color: #fff; font-size: 10.5px; font-weight: 600;
    line-height: 26px; text-align: center; border-radius: 2px;
  }

  .app-footer {
    position: absolute; left: 0; top: 1138px; width: 851px; height: 62px;
    background: var(--footer-bg); color: var(--footer-text);
    font-size: 8.3px; text-align: center; line-height: 68px;
  }
</style>
</head>
<body>

<svg class="symbols" aria-hidden="true">
  <symbol id="bullet-icon" viewBox="0 0 10 10">
    <circle cx="5" cy="5" r="5" fill="var(--bullet)"/>
    <path d="M4 2.8 6.2 5 4 7.2" stroke="#fff" stroke-width="1.5" fill="none"/>
  </symbol>
</svg>

<header class="app-header">
  <div class="menu-toggle"><span></span><span></span><span></span></div>
  <div class="brand"><span class="brand-mark"></span><span class="brand-name">Velqor</span></div>
  <nav class="header-actions">
    <svg viewBox="0 0 20 20" aria-label="Notifications"><path d="M10 1c-.8 0-1.4.6-1.4 1.3C5.9 3 4.5 5.3 4.5 8v4.5L2.5 15v1h15v-1l-2-2.5V8c0-2.7-1.4-5-4.1-5.7C11.4 1.6 10.8 1 10 1zM8 17a2 2 0 0 0 4 0z"/></svg>
    <svg viewBox="0 0 20 20" aria-label="Profile"><circle cx="10" cy="6" r="4.5"/><path d="M1.5 19c0-5 3.8-7.5 8.5-7.5s8.5 2.5 8.5 7.5z"/></svg>
    <svg viewBox="0 0 20 20" aria-label="Settings"><path d="M8.6 1h2.8l.4 2.4 1.6.7 2-1.4 2 2-1.4 2 .7 1.6 2.4.4v2.8l-2.4.4-.7 1.6 1.4 2-2 2-2-1.4-1.6.7-.4 2.4H8.6l-.4-2.4-1.6-.7-2 1.4-2-2 1.4-2-.7-1.6L1 11.4V8.6l2.4-.4.7-1.6-1.4-2 2-2 2 1.4 1.6-.7zM10 7a3 3 0 1 0 0 6 3 3 0 0 0 0-6z"/></svg>
  </nav>
</header>

<section class="panel overview">
  <h2 class="panel-title">PROCESSES OVERVIEW</h2>

  <div class="metric" style="left:17px">
    <svg viewBox="0 0 100 100">
      <circle cx="50" cy="50" r="43" fill="none" stroke="var(--ring-track)" stroke-width="9"/>
      <path d="M80.4 80.4 A43 43 0 1 1 50 7" fill="none" stroke="var(--ring-active)" stroke-width="9"/>
      <text x="50" y="59" text-anchor="middle" class="metric-value" fill="var(--ring-active)">85</text>
    </svg>
    <p class="metric-label">ACTIVE PROCESSES</p>
  </div>

  <div class="metric" style="left:195px">
    <svg viewBox="0 0 100 100">
      <circle cx="50" cy="50" r="43" fill="none" stroke="var(--ring-track)" stroke-width="9"/>
      <path d="M19.6 19.6 A43 43 0 0 1 80.4 19.6" fill="none" stroke="var(--ring-completed)" stroke-width="9"/>
      <text x="50" y="59" text-anchor="middle" class="metric-value" fill="var(--ring-completed)">20</text>
    </svg>
    <p class="metric-label">COMPLETED PROCESSES</p>
  </div>

  <div class="metric" style="left:368px">
    <svg viewBox="0 0 100 100">
      <circle cx="50" cy="50" r="43" fill="none" stroke="var(--ring-track)" stroke-width="9"/>
      <path d="M19.6 80.4 A43 43 0 0 1 77.6 17.1" fill="none" stroke="var(--ring-completion)" stroke-width="9"/>
      <text x="50" y="59" text-anchor="middle" class="metric-value" fill="var(--ring-completion)">55%</text>
    </svg>
    <p class="metric-label">COMPLETION</p>
  </div>

  <div class="metric" style="left:537px">
    <svg viewBox="0 0 100 100">
      <circle cx="50" cy="50" r="43" fill="none" stroke="var(--ring-track)" stroke-width="9"/>
      <path d="M68.2 11 A43 43 0 0 1 92.4 57.5" fill="none" stroke="var(--ring-expenses)" stroke-width="9"/>
      <text x="50" y="59" text-anchor="middle" class="metric-value" fill="var(--ring-expenses)">$10</text>
    </svg>
    <p class="metric-label">EXPENSES</p>
  </div>
</section>

<section class="panel activity">
  <h2 class="panel-title">ACTIVITY FEED</h2>

  <article class="feed-card" style="left:31px">
    <div class="feed-avatar" role="img" aria-label="Team member portrait"></div>
    <div class="feed-text">Quisquam est qui dolorem ipsum quia dolor sit amet,
      <div class="feed-meta"><i></i>20/5/2017 &nbsp;|&nbsp; <i class="person"></i>Dolorem</div>
    </div>
  </article>
  <article class="feed-card" style="left:258px">
    <div class="feed-avatar" role="img" aria-label="Team member portrait"></div>
    <div class="feed-text">Quisquam est qui dolorem ipsum quia dolor sit amet,
      <div class="feed-meta"><i></i>20/5/2017 &nbsp;|&nbsp; <i class="person"></i>Dolorem</div>
    </div>
  </article>
  <article class="feed-card" style="left:486px">
    <div class="feed-avatar" role="img" aria-label="Team member portrait"></div>
    <div class="feed-text">Quisquam est qui dolorem ipsum quia dolor sit amet,
      <div class="feed-meta"><i></i>20/5/2017 &nbsp;|&nbsp; <i class="person"></i>Dolorem</div>
    </div>
  </article>
</section>

<section class="process-grid">
  <article class="process-card">
    <div class="process-row"><svg class="bullet"><use href="#bullet-icon"/></svg>Process Name :&nbsp; Quisquam</div>
    <div class="process-row"><svg class="bullet"><use href="#bullet-icon"/></svg>Expenses :&nbsp; $55.00</div>
    <div class="process-row"><svg class="bullet"><use href="#bullet-icon"/></svg>Status Description</div>
    <p class="process-desc">Neque porro quisquam est qui dolorem ipsum quia dolor sit amet, consectetur,</p>
    <div class="process-row"><svg class="bullet"><use href="#bullet-icon"/></svg>Current Stage : Executive Negotiation</div>
  </article>
  <article class="process-card">
    <div class="process-row"><svg class="bullet"><use href="#bullet-icon"/></svg>Process Name :&nbsp; Quisquam</div>
    <div class="process-row"><svg class="bullet"><use href="#bullet-icon"/></svg>Expenses :&nbsp; $55.00</div>
    <div class="process-row"><svg class="bullet"><use href="#bullet-icon"/></svg>Status Description</div>
    <p class="process-desc">Neque porro quisquam est qui dolorem ipsum quia dolor sit amet, consectetur,</p>
    <div class="process-row"><svg class="bullet"><use href="#bullet-icon"/></svg>Current Stage : Executive Negotiation</div>
  </article>
  <article class="process-card">
    <div class="process-row"><svg class="bullet"><use href="#bullet-icon"/></svg>Process Name :&nbsp; Quisquam</div>
    <div class="process-row"><svg class="bullet"><use href="#bullet-icon"/></svg>Expenses :&nbsp; $55.00</div>
    <div class="process-row"><svg class="bullet"><use href="#bullet-icon"/></svg>Status Description</div>
    <p class="process-desc">Neque porro quisquam est qui dolorem ipsum quia dolor sit amet, consectetur,</p>
    <div class="process-row"><svg class="bullet"><use href="#bullet-icon"/></svg>Current Stage : Executive Negotiation</div>
  </article>
  <article class="process-card">
    <div class="process-row"><svg class="bullet"><use href="#bullet-icon"/></svg>Process Name :&nbsp; Quisquam</div>
    <div class="process-row"><svg class="bullet"><use href="#bullet-icon"/></svg>Expenses :&nbsp; $55.00</div>
    <div class="process-row"><svg class="bullet"><use href="#bullet-icon"/></svg>Status Description</div>
    <p class="process-desc">Neque porro quisquam est qui dolorem ipsum quia dolor sit amet, consectetur,</p>
    <div class="process-row"><svg class="bullet"><use href="#bullet-icon"/></svg>Current Stage : Executive Negotiation</div>
  </article>
  <article class="process-card">
    <div class="process-row"><svg class="bullet"><use href="#bullet-icon"/></svg>Process Name :&nbsp; Quisquam</div>
    <div class="process-row"><svg class="bullet"><use href="#bullet-icon"/></svg>Expenses :&nbsp; $55.00</div>
    <div class="process-row"><svg class="bullet"><use href="#bullet-icon"/></svg>Status Description</div>
    <p class="process-desc">Neque porro quisquam est qui dolorem ipsum quia dolor sit amet, consectetur,</p>
    <div class="process-row"><svg class="bullet"><use href="#bullet-icon"/></svg>Current Stage : Executive Negotiation</div>
  </article>
  <article class="process-card">
    <div class="process-row"><svg class="bullet"><use href="#bullet-icon"/></svg>Process Name :&nbsp; Quisquam</div>
    <div class="process-row"><svg class="bullet"><use href="#bullet-icon"/></svg>Expenses :&nbsp; $55.00</div>
    <div class="process-row"><svg class="bullet"><use href="#bullet-icon"/></svg>Status Description</div>
    <p class="process-desc">Neque porro quisquam est qui dolorem ipsum quia dolor sit amet, consectetur,</p>
    <div class="process-row"><svg class="bullet"><use href="#bullet-icon"/></svg>Current Stage : Executive Negotiation</div>
  </article>
  <article class="process-card">
    <div class="process-row"><svg class="bullet"><use href="#bullet-icon"/></svg>Process Name :&nbsp; Quisquam</div>
    <div class="process-row"><svg class="bullet"><use href="#bullet-icon"/></svg>Expenses :&nbsp; $55.00</div>
    <div class="process-row"><svg class="bullet"><use href="#bullet-icon"/></svg>Status Description</div>
    <p class="process-desc">Neque porro quisquam est qui dolorem ipsum quia dolor sit amet, consectetur,</p>
    <div class="process-row"><svg class="bullet"><use href="#bullet-icon"/></svg>Current Stage : Executive Negotiation</div>
  </article>
  <article class="process-card">
    <div class="process-row"><svg class="bullet"><use href="#bullet-icon"/></svg>Process Name :&nbsp; Quisquam</div>
    <div class="process-row"><svg class="bullet"><use href="#bullet-icon"/></svg>Expenses :&nbsp; $55.00</div>
    <div class="process-row"><svg class="bullet"><use href="#bullet-icon"/></svg>Status Description</div>
    <p class="process-desc">Neque porro quisquam est qui dolorem ipsum quia dolor sit amet, consectetur,</p>
    <div class="process-row"><svg class="bullet"><use href="#bullet-icon"/></svg>Current Stage : Executive Negotiation</div>
  </article>
  <article class="process-card">
    <div class="process-row"><svg class="bullet"><use href="#bullet-icon"/></svg>Process Name :&nbsp; Quisquam</div>
    <div class="process-row"><svg class="bullet"><use href="#bullet-icon"/></svg>Expenses :&nbsp; $55.00</div>
    <div class="process-row"><svg class="bullet"><use href="#bullet-icon"/></svg>Status Description</div>
    <p class="process-desc">Neque porro quisquam est qui dolorem ipsum quia dolor sit amet, consectetur,</p>
    <div class="process-row"><svg class="bullet"><use href="#bullet-icon"/></svg>Current Stage : Executive Negotiation</div>
  </article>
</section>

<nav class="pagination">
  <span class="wide">Prev</span>
  <span class="current">1</span><span>2</span><span>3</span><span>4</span><span>5</span><span>6</span><span>...</span><span>22</span>
  <span class="wide">Next</span>
</nav>
<div class="new-process">+ NEW PROCESS</div>

<footer class="app-footer">Copyright © 2017&nbsp; All Rights Reserved</footer>

</body>
</html>
```